Renny Oskow - Free Personalised Health Consultation - "One size does not fit all"

This flyer will be left on tables/seats at speaking events and seminars and used to attain leads.

Top half will have "SMS me for a FREE Personalised Health Consultation" and my picture (see www.rennyoskow-demo.com and pick most engaging photo) and underneath my contact details. It must have lines with "Notes:" halfway down so people can take notes at the seminar and lines on the back with my contact details again and "Notes: with lines.

I am having a business card also being designed by Artvane for same and would like the flyer and business card to carry a similar feel/look for consistency.

Below is the brief for the business card being designed:
Business Card for www.rennyoskow-demo.com site. It is a trust site and I use it for 1:1 relatable connections. It is the one I use for building intimate 1:1 trust building and Exec Coaching Services and programs for high wealth individuals and corporates. I also have a commercial programmatic site of my personal health products and services and programs for main stream one to many. www.steadyforwardliving-demo.com that can also provoke thought for the www.rennyoskow-demo.com business card. (mind you will get a separate business card for that site, but want to provide context). It has a logo which you may want to draw from in designing the rennyoskow business card which is personal and is about building my brand. There is also a rennyoskow personal PX page and rennyoskow business PX page. I am a Certified Talent Compass 3.1 Coach with Norvik and you can get a corporate brief of me on there to give you more context https://www.norvikcoachhub-demo.com/coach/en-us/directory?search=renny

Target Market(s)

Exec, IT, Health conscious. Corporates wanting to run Health and Wellness programs. Those wanting to go from good to great. Millennials to Middleaged.

Industry/Entity Type

Health And Wellness

Font styles to use
Sans Serif
Other font styles liked:
• Arial and Calibri ok too

Colors

Designer to choose colors to be used in the design.

Requirements
Must have
• Picture of me - use best from www.rennyoskow-demo.com or can send one you choose.
• Contact details like my buisness card being designed by you guys in separate project.
• Name: Renny Oskow
• email: renny@rennyoskow-demo.,com
• Phone: Australia +61 400 000 137 Singapore: +65 9000 2468
Nice to have
• Open to ideas

```html
<!DOCTYPE html>
<html lang="en">
<head>
<meta charset="utf-8">
<title>Renny Oskow – Health Consultation Notes Flyer</title>
<link rel="stylesheet" href="https://fonts.googleapis.com/css2?family=Archivo:wght@800;900&family=Arimo:wght@400;700&display=swap">
<style>
  :root {
    --stage: #000000;
    --paper: #ffffff;
    --brand-blue: #00a9e6;
    --brand-blue-light: #1fb6ec;
    --bubble: #cdeaf8;
    --soft-grey: #ececec;
    --rule: #cfcfcf;
    --ink: #000000;
    --photo-light: #d9d9d9;
    --photo-dark: #5a5a5a;
    --sign-tone: #e4e4e4;
  }
  * { margin: 0; padding: 0; box-sizing: border-box; }
  html, body {
    width: 1200px; height: 835px; overflow: hidden;
    background: var(--stage);
  }
  .canvas { position: relative; width: 1200px; height: 835px; }

  .sheet {
    position: absolute; top: 77px;
    width: 483px; height: 682px;
    background: var(--paper);
    overflow: hidden;
  }
  .sheet--front { left: 88px; }
  .sheet--back { left: 629px; }

  .circle { position: absolute; border-radius: 50%; }
  .front-grey-circle { left: 216px; top: 28px; width: 230px; height: 230px; background: var(--soft-grey); }
  .front-blue-circle { left: 51px; top: 113px; width: 126px; height: 126px; background: var(--brand-blue); }
  .bubble-large { left: 422px; top: 41px; width: 26px; height: 26px; background: var(--bubble); }
  .bubble-small { left: 438px; top: 69px; width: 10px; height: 10px; background: var(--bubble); }

  .portrait {
    position: absolute;
    background: linear-gradient(180deg, var(--photo-light) 0%, #a9a9a9 45%, var(--photo-dark) 100%);
  }
  .front-portrait { left: 58px; top: 12px; width: 256px; height: 220px; border-radius: 110px 110px 0 0; }
  .back-portrait { left: 0; top: 472px; width: 128px; height: 146px; border-radius: 64px 64px 0 0; }

  .signature {
    position: absolute;
    background: var(--sign-tone);
    border-radius: 4px;
  }
  .front-signature { left: 236px; top: 118px; width: 176px; height: 28px; }
  .back-signature { left: 380px; top: 621px; width: 94px; height: 24px; }

  .promo-band { position: absolute; left: 0; top: 232px; width: 483px; height: 210px; }
  .band-rule { position: absolute; left: 60px; top: 263px; width: 1px; height: 172px; background: rgba(255,255,255,0.7); }

  .headline {
    position: absolute; left: 79px; top: 257px;
    font-family: "Archivo", "Arial Black", sans-serif;
    font-weight: 900; color: var(--paper);
    text-transform: uppercase; letter-spacing: 0.5px;
  }
  .headline-line { display: block; white-space: nowrap; }
  .headline-big { font-size: 38px; line-height: 44px; }
  .headline-small { font-size: 25px; }
  .headline-mid { font-size: 26.5px; line-height: 40px; }
  .free-tag {
    display: inline-block;
    background: var(--paper); color: var(--ink);
    padding: 0 6px; line-height: 28px;
  }

  .contact-bar {
    position: absolute; height: 48px;
    background: var(--ink);
    display: flex; align-items: center;
    font-family: "Arimo", Arial, sans-serif;
    font-size: 8.4px;
    color: var(--paper); text-transform: uppercase;
    clip-path: polygon(0 0, 100% 0, 96% 100%, 0 100%);
  }
  .front-contact { left: 77px; top: 395px; width: 378px; }
  .back-contact { left: 0; top: 618px; width: 374px; }
  .contact-group { display: flex; flex-direction: column; gap: 7px; }
  .contact-group--phones { padding-left: 14px; width: 162px; }
  .contact-group--web { padding-left: 10px; border-left: 1px solid rgba(255,255,255,0.8); }
  .contact-row { display: flex; align-items: center; gap: 6px; white-space: nowrap; }
  .contact-icon { width: 8px; height: 8px; flex: none; }
  .icon-spacer { width: 8px; flex: none; }

  .notes-lines { position: absolute; left: 19px; }
  .notes-line { position: absolute; left: 0; height: 1px; background: var(--rule); }

  .back-grey-circle { left: 355px; top: 575px; width: 124px; height: 124px; background: var(--soft-grey); }
  .back-blue-strip { position: absolute; left: 0; top: 650px; width: 483px; height: 32px; background: var(--brand-blue); }
  .signature-underline { position: absolute; left: 384px; top: 648px; width: 92px; height: 1px; background: #6b6b9a; }
</style>
</head>
<body>
<main class="canvas">

  <section class="sheet sheet--front" aria-label="Flyer front">
    <div class="circle front-grey-circle"></div>
    <div class="circle front-blue-circle"></div>
    <div class="circle bubble-large"></div>
    <div class="circle bubble-small"></div>

    <div class="portrait front-portrait" role="img" aria-label="Black and white portrait photo of Renny Oskow smiling, wearing a dark v-neck t-shirt"></div>
    <div class="signature front-signature" role="img" aria-label="Handwritten signature: Renny Oskow"></div>

    <svg class="promo-band" viewBox="0 0 483 210" aria-hidden="true">
      <polygon points="0,0 483,0 483,165 0,209" fill="var(--brand-blue)"/>
      <polygon points="0,150 483,95 483,165 0,209" fill="var(--brand-blue-light)"/>
    </svg>
    <div class="band-rule"></div>

    <h1 class="headline">
      <span class="headline-line headline-big">SMS me <span class="headline-small">for</span></span>
      <span class="headline-line headline-mid">A <span class="free-tag">Free</span> Personalised</span>
      <span class="headline-line headline-mid">Health Consultation</span>
    </h1>

    <div class="contact-bar front-contact">
      <div class="contact-group contact-group--phones">
        <div class="contact-row">
          <svg class="contact-icon" viewBox="0 0 10 10"><path d="M2.2 0.6 L3.6 2.6 L2.8 3.6 Q4 6 6.4 7.2 L7.4 6.4 L9.4 7.8 L8.4 9.4 Q3.6 9 0.6 1.6 Z" fill="#fff"/></svg>
          <span>Australia:&nbsp; +61 400 000 137</span>
        </div>
        <div class="contact-row">
          <span class="icon-spacer"></span>
          <span>Singapore: +65 9000 2468</span>
        </div>
      </div>
      <div class="contact-group contact-group--web">
        <div class="contact-row">
          <svg class="contact-icon" viewBox="0 0 10 10"><rect x="0.5" y="2" width="9" height="6" fill="#fff"/><path d="M0.5 2 L5 5.5 L9.5 2" stroke="#000" stroke-width="0.9" fill="none"/></svg>
          <span>renny@rennyoskow-demo.com</span>
        </div>
        <div class="contact-row">
          <svg class="contact-icon" viewBox="0 0 10 10"><circle cx="5" cy="5" r="4.5" fill="#fff"/><path d="M0.5 5 H9.5 M5 0.5 Q2.4 5 5 9.5 M5 0.5 Q7.6 5 5 9.5" stroke="#000" stroke-width="0.7" fill="none"/></svg>
          <span>www.rennyoskow-demo.com</span>
        </div>
      </div>
    </div>

    <div class="notes-lines" style="top:475px;">
      <div class="notes-line" style="top:0;width:445px"></div>
      <div class="notes-line" style="top:27px;width:445px"></div>
      <div class="notes-line" style="top:54px;width:445px"></div>
      <div class="notes-line" style="top:81px;width:445px"></div>
      <div class="notes-line" style="top:108px;width:445px"></div>
      <div class="notes-line" style="top:135px;width:445px"></div>
      <div class="notes-line" style="top:162px;width:445px"></div>
      <div class="notes-line" style="top:189px;width:445px"></div>
    </div>
  </section>

  <section class="sheet sheet--back" aria-label="Flyer back">
    <div class="circle back-grey-circle"></div>

    <div class="notes-lines" style="top:32px;">
      <div class="notes-line" style="top:0;width:445px"></div>
      <div class="notes-line" style="top:27px;width:445px"></div>
      <div class="notes-line" style="top:54px;width:445px"></div>
      <div class="notes-line" style="top:81px;width:445px"></div>
      <div class="notes-line" style="top:108px;width:445px"></div>
      <div class="notes-line" style="top:135px;width:445px"></div>
      <div class="notes-line" style="top:162px;width:445px"></div>
      <div class="notes-line" style="top:189px;width:445px"></div>
      <div class="notes-line" style="top:216px;width:445px"></div>
      <div class="notes-line" style="top:243px;width:445px"></div>
      <div class="notes-line" style="top:270px;width:445px"></div>
      <div class="notes-line" style="top:297px;width:445px"></div>
      <div class="notes-line" style="top:324px;width:445px"></div>
      <div class="notes-line" style="top:351px;width:445px"></div>
      <div class="notes-line" style="top:378px;width:445px"></div>
      <div class="notes-line" style="top:405px;width:445px"></div>
      <div class="notes-line" style="top:431px;width:445px"></div>
      <div class="notes-line" style="top:458px;left:64px;width:381px"></div>
      <div class="notes-line" style="top:485px;left:80px;width:365px"></div>
      <div class="notes-line" style="top:512px;left:97px;width:348px"></div>
      <div class="notes-line" style="top:539px;left:105px;width:340px"></div>
      <div class="notes-line" style="top:566px;left:115px;width:330px"></div>
    </div>

    <div class="portrait back-portrait" role="img" aria-label="Black and white photo of Renny Oskow smiling with arms crossed, wearing a dark t-shirt"></div>

    <div class="back-blue-strip"></div>

    <div class="contact-bar back-contact">
      <div class="contact-group contact-group--phones">
        <div class="contact-row">
          <svg class="contact-icon" viewBox="0 0 10 10"><path d="M2.2 0.6 L3.6 2.6 L2.8 3.6 Q4 6 6.4 7.2 L7.4 6.4 L9.4 7.8 L8.4 9.4 Q3.6 9 0.6 1.6 Z" fill="#fff"/></svg>
          <span>Australia:&nbsp; +61 400 000 137</span>
        </div>
        <div class="contact-row">
          <span class="icon-spacer"></span>
          <span>Singapore: +65 9000 2468</span>
        </div>
      </div>
      <div class="contact-group contact-group--web">
        <div class="contact-row">
          <svg class="contact-icon" viewBox="0 0 10 10"><rect x="0.5" y="2" width="9" height="6" fill="#fff"/><path d="M0.5 2 L5 5.5 L9.5 2" stroke="#000" stroke-width="0.9" fill="none"/></svg>
          <span>renny@rennyoskow-demo.com</span>
        </div>
        <div class="contact-row">
          <svg class="contact-icon" viewBox="0 0 10 10"><circle cx="5" cy="5" r="4.5" fill="#fff"/><path d="M0.5 5 H9.5 M5 0.5 Q2.4 5 5 9.5 M5 0.5 Q7.6 5 5 9.5" stroke="#000" stroke-width="0.7" fill="none"/></svg>
          <span>www.rennyoskow-demo.com</span>
        </div>
      </div>
    </div>

    <div class="signature back-signature" role="img" aria-label="Handwritten signature: Renny Oskow"></div>
    <div class="signature-underline"></div>
  </section>

</main>
</body>
</html>
```